Sophisticated, clean website reflecting my feminine, playful side to sell my abstract art,

I need a website no more than 3 pages to showcase my paintings, a little about me and some contact info. I do abstracts so looking for something a little edgy, yet feminine and current.
Updates

Hi there, These are some artists websites that I Iike: Marnelvoss.com (I like how airy it is) peterwallombry.com garethpolvens.com (I like how it scrolls) I'll need a place for a photo ( a headshot-i do not have it yet so I'll need to be able to upload that later) as well as an area for my bio. Also, it's important that I will be able to upload any new photos and descriptions easily so it should be user friendly. Lastly, I like in a sunny place so would like to have this seem upbeat and playful as that is how i like to paint. thanks-I'm trying to upload my photos now -

Target Market(s)

ppl ages 35-70 who want large scale art for their homes

Industry/Entity Type

art

Coding

Coded - Design and coding required

Number of Pages Required

3 page

Colors

Designer to choose colors to be used in the design.

Requirements
Must have
• photos of my art, a place for my bio, be easy to reach me. tasteful-nothing too "in your face" -my clients are pretty high end and organized. They like clean lines
Nice to have
• sophisticated background, muted tones in the back-similar clean font throughout-no cursive
Should not have
• too many dark areas. Too many blocks of color. Too serious.

```html
<!DOCTYPE html>
<html lang="en">
<head>
<meta charset="utf-8">
<title>Helena Sorell Art</title>
<link href="https://fonts.googleapis.com/css2?family=Oswald:wght@300;400;500&family=Open+Sans:wght@400;600&display=swap" rel="stylesheet">
<style>
:root{
  --ink:#1d1d1d;
  --muted:#6f6f6f;
  --rule:#c9c9c9;
  --paper:#ffffff;
  --field-line:#9a9a9a;
}
*{box-sizing:border-box;margin:0;padding:0}
html,body{width:1200px;height:4816px;overflow:hidden;background:var(--paper)}
body{position:relative;font-family:"Open Sans",Arial,sans-serif;color:var(--ink)}
.page{position:static}
.brand{position:absolute;left:0;width:1200px;height:64px;display:flex;justify-content:center;align-items:center;gap:14px}
.brand span{font-family:"Oswald",Arial,sans-serif;font-weight:400;font-size:12px;letter-spacing:2px;color:var(--ink)}
.brand i{display:block;width:40px;height:56px;background:var(--ink)}
.nav{position:absolute;left:0;width:1200px;height:28px;display:flex;justify-content:center;gap:54px;font-family:"Oswald",Arial,sans-serif;font-weight:300;font-size:20px;line-height:28px;color:var(--muted);letter-spacing:.5px}
.nav .active{color:var(--ink);font-weight:400}
.nav-rule{position:absolute;left:470px;width:260px;height:1px;background:var(--rule)}
.footer{position:absolute;left:0;width:1200px;text-align:center;font-size:10px;line-height:14px;color:var(--muted)}
.art{position:absolute}
.hero{left:40px;top:188px;width:1120px;height:572px;background:
 radial-gradient(ellipse 220px 140px at 35% 25%,#d9b54a 0%,rgba(217,181,74,0) 100%),
 radial-gradient(ellipse 260px 120px at 70% 60%,#1f6c8a 0%,rgba(31,108,138,0) 100%),
 radial-gradient(ellipse 300px 200px at 20% 70%,#2f8a3c 0%,rgba(47,138,60,0) 100%),
 linear-gradient(120deg,#5fae5a,#b9d27a 40%,#3f9a52 70%,#e7e4d6)}
.hero-fade{position:absolute;left:40px;top:760px;width:1120px;height:80px;background:linear-gradient(#e7efe2,rgba(255,255,255,0))}
.slide-arrow{position:absolute;top:460px;width:32px;height:32px}
.portrait{left:40px;width:424px;background:linear-gradient(160deg,#e9e6e3,#cdbfb3 55%,#8a6a55);border:1px solid #8e8e8e}
.copy{position:absolute;font-size:12px;line-height:20px;color:#333}
.signature{left:500px;top:1204px;width:110px;height:64px;background:linear-gradient(90deg,#dedede,#f2f2f2)}
.view-link{position:absolute;left:220px;top:1476px;display:flex;align-items:center;gap:12px;font-family:"Oswald",Arial,sans-serif;font-weight:500;font-size:13px;letter-spacing:1px;color:var(--ink)}
.view-link i{display:block;width:24px;height:24px;border:1px solid var(--ink);border-radius:50%}
.tile{position:absolute;width:288px;height:384px}
.caption{position:absolute;width:288px;text-align:center;font-family:"Oswald",Arial,sans-serif;font-size:14px;font-weight:400}
.info-card{position:absolute;left:290px;top:1948px;width:252px;height:340px;background:rgba(255,255,255,.93);padding:26px 22px}
.info-card h3{font-family:"Oswald",Arial,sans-serif;font-weight:400;font-size:16px;padding-bottom:12px;border-bottom:1px solid var(--rule)}
.info-row{display:flex;align-items:center;gap:12px;margin-top:26px;font-size:12px;color:#444}
.box{width:16px;height:16px;border:1px solid #666}
.bullets{list-style:none}
.bullets li{display:flex;gap:12px;align-items:center;font-size:12px;line-height:26px}
.bullets li::before{content:"";flex:none;width:8px;height:8px;background:var(--ink);border-radius:50%}
.contact-line{position:absolute;left:496px;top:3638px;display:flex;align-items:center;gap:12px;font-size:12px}
.socials{position:absolute;display:flex;gap:14px}
.socials i{display:block;width:24px;height:24px;border:1.5px solid var(--ink);border-radius:50%}
.field{position:absolute;left:392px;width:416px;border-bottom:1px solid var(--field-line);font-size:11px;color:var(--muted);padding-bottom:6px}
.send{position:absolute;left:392px;top:4536px;width:416px;height:44px;background:var(--ink);color:#fff;font-family:"Oswald",Arial,sans-serif;font-size:14px;letter-spacing:1px;display:flex;align-items:center;justify-content:center}
.note{position:absolute;left:0;width:1200px;text-align:center;font-size:10px;color:var(--muted)}
</style>
</head>
<body>

<section class="page home">
  <div class="brand" style="top:28px"><span>HELENA</span><i></i><span>SORELL</span></div>
  <nav class="nav" style="top:134px"><span>GALLERY</span><span>ABOUT</span><span>CONTACT</span></nav>
  <div class="nav-rule" style="top:168px"></div>
  <div class="art hero" role="img" aria-label="Featured abstract painting in greens, yellow and blue"></div>
  <div class="hero-fade"></div>
  <svg class="slide-arrow" style="left:56px" viewBox="0 0 32 32"><path d="M20 6 10 16l10 10" fill="none" stroke="#111" stroke-width="3"/></svg>
  <svg class="slide-arrow" style="left:1112px" viewBox="0 0 32 32"><path d="M12 6l10 10-10 10" fill="none" stroke="#111" stroke-width="3"/></svg>
  <div class="art portrait" style="top:876px;height:572px" role="img" aria-label="Portrait photo of the artist"></div>
  <p class="copy" style="left:496px;top:1060px;width:390px">Lorem ipsum dolor sit amet, consectetuer adipiscing elit. Aenean commodo ligula eget dolor. Aenean massa. Cum sociis natoque penatibus et magnis dis parturient montes, nascetur ridiculus mus. Donec quam felis, ultricies nec, pellentesque eu, pretium quis, sem. Nulla consequat massa quis enim.</p>
  <div class="art signature" role="img" aria-label="Artist's handwritten signature"></div>
  <a class="view-link"><span>VIEW GALLERY</span><i></i></a>
  <p class="footer" style="top:1618px">©2022 Helena Sorell Art. All rights reserved</p>
</section>

<section class="page gallery">
  <div class="brand" style="top:1712px"><span>HELENA</span><i></i><span>SORELL</span></div>
  <nav class="nav" style="top:1818px"><span class="active">GALLERY</span><span>ABOUT</span><span>CONTACT</span></nav>
  <div class="nav-rule" style="top:1852px"></div>
  <div class="art tile" style="left:272px;top:1928px;background:linear-gradient(135deg,#7a4d6a,#d9b9c3 45%,#efe6e6 60%,#6b3d5a)" role="img" aria-label="Abstract painting in plum and blush"></div>
  <div class="info-card">
    <h3>Donec pede justo</h3>
    <div class="info-row"><svg width="16" height="16" viewBox="0 0 16 16"><path d="M2 14 14 2M10 2h4v4" fill="none" stroke="#444" stroke-width="1.5"/></svg><span>12 × 48 / 48</span></div>
    <div class="info-row"><span class="box"></span><span>Mauris mattis on canvas</span></div>
  </div>
  <div class="art tile" style="left:640px;top:1928px;background:linear-gradient(180deg,#e6dccb,#d8c8ae 45%,#6f5a3e 60%,#2f7fa6 85%,#e8e4dc)" role="img" aria-label="Abstract painting with blue drips on sand tones"></div>
  <p class="caption" style="left:272px;top:2328px">Donec pede justo</p>
  <p class="caption" style="left:640px;top:2328px">In enim justo</p>
  <div class="art tile" style="left:272px;top:2388px;background:radial-gradient(circle at 50% 55%,#f1ece3 0%,#2f8f86 35%,#c6612e 60%,#1f4f6a 90%)" role="img" aria-label="Abstract painting in teal and orange"></div>
  <div class="art tile" style="left:640px;top:2388px;background:radial-gradient(circle at 45% 50%,#f0e2c2 0%,#d4a43a 35%,#b7442e 60%,#2c5c8c 85%)" role="img" aria-label="Abstract painting in yellow, red and blue"></div>
  <p class="caption" style="left:272px;top:2788px">Integer tincidunt</p>
  <p class="caption" style="left:640px;top:2788px">Cras dapibus</p>
  <p class="footer" style="top:3106px">©2022 Helena Sorell Art. All rights reserved</p>
</section>

<section class="page about">
  <div class="brand" style="top:3196px"><span>HELENA</span><i></i><span>SORELL</span></div>
  <nav class="nav" style="top:3302px"><span>GALLERY</span><span class="active">ABOUT</span><span>CONTACT</span></nav>
  <div class="nav-rule" style="top:3336px"></div>
  <div class="art portrait" style="top:3408px;height:520px" role="img" aria-label="Portrait photo of the artist"></div>
  <p class="copy" style="left:496px;top:3404px;width:420px">Lorem ipsum dolor sit amet, consectetuer adipiscing elit. Aenean commodo ligula eget dolor. Aenean massa. Cum sociis natoque penatibus et magnis dis parturient montes, nascetur ridiculus mus. Donec quam felis, ultricies nec, pellentesque eu, pretium quis, sem. Nulla consequat massa quis enim.</p>
  <ul class="bullets copy" style="left:496px;top:3510px;width:440px">
    <li>Donec pede justo, fringilla vel, aliquet nec, vulputate eget, arcu.</li>
    <li>In enim justo, rhoncus ut, imperdiet a, venenatis vitae, justo.</li>
    <li>Aenean leo ligula, porttitor eu, consequat vitae, eleifend ac, enim.</li>
  </ul>
  <div class="contact-line"><svg width="16" height="12" viewBox="0 0 16 12"><rect x=".5" y=".5" width="15" height="11" fill="none" stroke="#1d1d1d"/><path d="M.5.5 8 7 15.5.5" fill="none" stroke="#1d1d1d"/></svg><span>contact@helenasorellart.com</span></div>
  <div class="socials" style="left:496px;top:3682px" aria-label="Social profiles"><i></i><i></i></div>
  <p class="footer" style="top:3990px">©2022 Helena Sorell Art. All rights reserved</p>
</section>

<section class="page contact">
  <div class="brand" style="top:4084px"><span>HELENA</span><i></i><span>SORELL</span></div>
  <nav class="nav" style="top:4194px"><span>GALLERY</span><span>ABOUT</span><span class="active">CONTACT</span></nav>
  <div class="nav-rule" style="top:4228px"></div>
  <div class="field" style="top:4296px">* First Name</div>
  <div class="field" style="top:4340px">* Last Name</div>
  <div class="field" style="top:4384px">* Email</div>
  <div class="field" style="top:4436px;height:60px">* Message</div>
  <div class="send">SEND MESSAGE</div>
  <p class="note" style="top:4598px">Follow us on social networks</p>
  <div class="socials" style="left:562px;top:4640px" aria-label="Social profiles"><i></i><i></i></div>
  <p class="footer" style="top:4786px">©2022 Helena Sorell Art. All rights reserved</p>
</section>

</body>
</html>
```